Looking for someone to design a business card for my plumbing business Quandor Plumbing Solutions I want the background also to be black, must attract clients. If possible I want the front to be the logo and the back to show maybe the details.

Target Market(s)

Clients

Industry/Entity Type

Plumbing maintenance

Contact Information for Business Card

Name: Felix, Contact: 0461 539 207, Email: quandorplumbingsolutions@mailbrook.example, Licence number 728093K

Font styles to use
Other font styles liked:
• as per logo maybe?

Colors

Designer to choose colors to be used in the design.

Requirements
Nice to have
• stating the service I provide, emergency plumbing, plumbing maintenance, drainage maintenance, block sewer and stormwater, camera and locating.

```html
<!DOCTYPE html>
<html lang="en">
<head>
<meta charset="utf-8">
<title>Quandor Plumbing Solutions – Business Card</title>
<link rel="stylesheet" href="https://fonts.googleapis.com/css2?family=Montserrat:wght@400;500;800&display=swap">
<style>
  :root {
    --stage: #3b3b3b;
    --card: #121212;
    --card-edge: #1c1c1c;
    --white: #f4f4f4;
    --blue: #4a90d6;
    --muted: #e6e6e6;
  }
  * { box-sizing: border-box; margin: 0; padding: 0; }
  html, body { width: 1200px; height: 689px; overflow: hidden; }
  body {
    background: var(--stage);
    font-family: "Montserrat", sans-serif;
    position: relative;
  }
  .card {
    position: absolute;
    top: 176px;
    width: 550px;
    height: 336px;
    background: var(--card);
    border-radius: 22px;
    border: 1px solid var(--card-edge);
    box-shadow: 0 18px 40px rgba(0,0,0,0.45);
    overflow: hidden;
  }
  .card--front { left: 35px; }
  .card--back { left: 615px; }

  /* Front: brand name set as text */
  .front-brand {
    position: absolute;
    inset: 0;
    display: flex;
    align-items: center;
    justify-content: center;
    gap: 16px;
  }
  .brand-dot {
    width: 22px; height: 22px;
    border-radius: 50%;
    background: var(--white);
    flex: none;
  }
  .brand-name {
    font-weight: 800;
    color: var(--white);
    text-transform: uppercase;
    line-height: 1.05;
  }
  .front-brand .brand-name { font-size: 34px; }

  /* Back: brand left, details right */
  .back-brand {
    position: absolute;
    left: 28px;
    top: 0; bottom: 0;
    width: 190px;
    display: flex;
    align-items: center;
    gap: 10px;
  }
  .back-brand .brand-dot { width: 14px; height: 14px; background: var(--blue); }
  .back-brand .brand-name { font-size: 19px; color: var(--blue); }

  .divider {
    position: absolute;
    left: 232px;
    top: 92px;
    width: 2px;
    height: 152px;
    background: var(--blue);
  }
  .details {
    position: absolute;
    left: 250px;
    top: 92px;
    right: 14px;
    color: var(--muted);
  }
  .details__name {
    font-weight: 800;
    font-size: 28px;
    color: var(--blue);
    line-height: 1;
    margin-bottom: 18px;
  }
  .details__licence {
    font-size: 13px;
    font-weight: 500;
    margin-bottom: 28px;
  }
  .contact {
    list-style: none;
    font-size: 11px;
    font-weight: 500;
  }
  .contact li {
    display: flex;
    align-items: center;
    gap: 8px;
    margin-bottom: 10px;
    white-space: nowrap;
  }
  .contact li:first-child { font-size: 14px; }
  .contact svg { width: 13px; height: 13px; flex: none; fill: var(--blue); }
</style>
</head>
<body>

<section class="card card--front" aria-label="Card front">
  <div class="front-brand">
    <span class="brand-dot"></span>
    <span class="brand-name">Quandor<br>Plumbing Solutions</span>
  </div>
</section>

<section class="card card--back" aria-label="Card back">
  <div class="back-brand">
    <span class="brand-dot"></span>
    <span class="brand-name">Quandor<br>Plumbing<br>Solutions</span>
  </div>
  <div class="divider"></div>
  <div class="details">
    <p class="details__name">Felix</p>
    <p class="details__licence">Licence number 728093K</p>
    <ul class="contact">
      <li>
        <svg viewBox="0 0 24 24" aria-hidden="true"><path d="M6.6 10.8a15.1 15.1 0 0 0 6.6 6.6l2.2-2.2a1 1 0 0 1 1-.25 11.4 11.4 0 0 0 3.6.57 1 1 0 0 1 1 1V20a1 1 0 0 1-1 1A17 17 0 0 1 3 4a1 1 0 0 1 1-1h3.5a1 1 0 0 1 1 1c0 1.25.2 2.45.57 3.6a1 1 0 0 1-.25 1z"/></svg>
        0461 539 207
      </li>
      <li>
        <svg viewBox="0 0 24 24" aria-hidden="true"><path d="M2 5h20v14H2z M4 7v.5l8 5 8-5V7l-8 5z" fill-rule="evenodd"/></svg>
        quandorplumbingsolutions@mailbrook.example
      </li>
    </ul>
  </div>
</section>

</body>
</html>
```